Facebook Header Design Project.

I'm supplying white and colored logos. The Facebook page already exists. URL = https://www.brindlepost.example/quillarc.studio The design should not be based on what's already there. Consider mobile implications of the design. This Design will form the designs of other social media headers. QuillArc is a web design | digital marketing company.

Target Market(s)

People interested in web design | digital marketing services.

Industry/Entity Type

QuillArc is a web design | digital marketing company. That should be clear in the design.

Colors
0054AA
0677BA
7BADD7
CADEEF
E8F1F8

Requirements
Must have
• Logo. Use Facebook header image dimension.
Nice to have
• Use a color scheme like the logo and feel free to add a color or two from the other side of the color whee.

```html
<!DOCTYPE html>
<html lang="en">
<head>
<meta charset="UTF-8">
<title>QuillArc – Facebook Header</title>
<link rel="stylesheet" href="https://fonts.googleapis.com/css2?family=Outfit:wght@300;700&family=Open+Sans:wght@700&display=swap">
<style>
  :root {
    --stage: #d0d0d0;
    --paper: #ffffff;
    --brand-blue: #4677ba;
    --headline-navy: #3d5296;
    --ink: #222222;
    --pill-blue: #0660a4;
    --photo-deep: #0f1c2c;
    --photo-mid: #3a5872;
  }
  * { margin: 0; padding: 0; box-sizing: border-box; }
  html, body {
    width: 1200px; height: 1200px; overflow: hidden;
    background: var(--stage);
  }
  .cover {
    position: absolute; left: 102px; top: 376px;
    width: 996px; height: 416px;
    background: var(--paper);
    overflow: hidden;
  }
  .cover-art { position: absolute; inset: 0; width: 996px; height: 416px; }
  .brand-name {
    position: absolute; left: 590px; top: 64px;
    font: 700 38px/1 "Outfit", sans-serif;
    color: var(--brand-blue);
    display: flex; align-items: center; gap: 10px;
  }
  .brand-dot {
    width: 14px; height: 14px; border-radius: 50%;
    background: var(--brand-blue);
  }
  .tagline {
    position: absolute; left: 482px; top: 150px;
    font-family: "Outfit", sans-serif;
    text-transform: uppercase;
  }
  .tagline-lead {
    display: block;
    font-weight: 300; font-size: 48px; line-height: 50px;
    color: var(--ink); letter-spacing: -0.5px;
  }
  .tagline-focus {
    display: block;
    font-weight: 700; font-size: 46px; line-height: 47px;
    color: var(--headline-navy); letter-spacing: -0.5px;
  }
  .handle-pill {
    position: absolute; left: 470px; top: 317px;
    width: 288px; height: 42px; border-radius: 21px;
    background: var(--pill-blue);
    color: #fff;
    font: 700 20px/42px "Open Sans", sans-serif;
    letter-spacing: 3px;
    padding-left: 36px;
    white-space: nowrap;
  }
</style>
</head>
<body>
  <div class="cover">
    <svg class="cover-art" viewBox="0 0 1604 670" preserveAspectRatio="none" xmlns="http://www.w3.org/2000/svg">
      <defs>
        <linearGradient id="photoTone" x1="0" y1="0" x2="0" y2="1">
          <stop offset="0" stop-color="var(--photo-mid)"/>
          <stop offset="0.5" stop-color="#52606c"/>
          <stop offset="1" stop-color="var(--photo-deep)"/>
        </linearGradient>
      </defs>

      <path class="brand-wash" fill="var(--brand-blue)"
        d="M0 0 H786 C750 140 690 230 600 300 L112 425 C70 418 30 405 0 390 Z"/>

      <circle class="photo-frame" cx="400" cy="331" r="298" fill="#ffffff"/>
      <g class="photo-hero" role="img" aria-label="Photo of business people in silhouette shaking hands in an office, overlaid with digital marketing icons for video, blog, ads, website and growth charts">
        <circle cx="400" cy="331" r="290" fill="url(#photoTone)"/>
      </g>
    </svg>

    <div class="brand-name"><span class="brand-dot"></span>QuillArc</div>

    <h1 class="tagline">
      <span class="tagline-lead">We make</span>
      <span class="tagline-focus">Digital marketing</span>
      <span class="tagline-focus">Simple</span>
    </h1>

    <div class="handle-pill">@quillarc.studio</div>
  </div>
</body>
</html>
```